RM Installations Web Site Design

Need a basic site to show clients a little about what we do. We are a custom audio video company in the high-end residential market. Need a few basic but professional pages to show past projects and products we sell. No e-commerce. Should include my new logo from MarkBazaar.

Industry/Entity Type

Residential

Number of Pages Required

2 page

Font styles to use
Serif
Sans Serif

Colors
f78f20

Requirements
Must have
• Company Logo, Send feedback page
Nice to have
• I have no ideas about design, but I do know what I like and dislike when I see it.

```html
<!DOCTYPE html>
<html lang="en">
<head>
<meta charset="utf-8">
<title>RM Installations</title>
<link href="https://fonts.googleapis.com/css2?family=Lato:wght@400;700&family=Oswald:wght@400&display=swap" rel="stylesheet">
<style>
:root{
  --orange:#f78f20;
  --orange-dark:#d9741a;
  --ink:#333333;
  --topbar:#3b3b3b;
  --grey-bg:#f0f0f0;
  --white:#ffffff;
  --muted:#555555;
}
*{box-sizing:border-box;margin:0;padding:0}
html,body{width:1200px;height:2163px;overflow:hidden;background:var(--white)}
body{position:relative;font-family:'Lato',sans-serif;color:var(--ink)}
.abs{position:absolute}
.topbar{left:0;top:0;width:1200px;height:26px;background:var(--topbar);color:#eee;font-size:12px}
.topbar .contact{top:6px;display:flex;align-items:center;gap:6px}
.feedback{left:932px;top:0;width:92px;height:26px;background:var(--orange);color:#fff;font-size:12px;text-align:center;line-height:28px}
.header{left:0;top:26px;width:1200px;height:76px;background:var(--white)}
.brand{left:170px;top:24px;font-size:24px;font-weight:700;color:var(--ink);line-height:28px}
.nav{top:0;height:76px;font-size:11.5px;color:#444;line-height:86px;white-space:nowrap}
.nav.active{background:var(--orange);color:#fff;width:70px;text-align:center}
.hero{left:0;top:102px;width:1200px;height:446px;background:radial-gradient(ellipse at 45% 40%,#5a5a5a 0%,#2a2a2a 45%,#111 75%),#111}
.hero h1{position:absolute;left:0;width:1200px;top:345px;text-align:center;font-family:'Oswald',sans-serif;font-weight:400;font-size:58px;color:#fff;letter-spacing:.5px}
.hero-arrow{top:248px;width:44px;height:60px;background:rgba(255,255,255,.25)}
.section-title{left:0;width:1200px;text-align:center;font-size:26px;font-weight:400}
.section-title em{font-style:normal;color:var(--orange)}
.rule{height:1px;background:#e2e2e2;left:444px;width:312px}
.about-text{left:175px;top:700px;width:850px;text-align:center;font-size:13px;line-height:21.5px;color:var(--muted)}
.btn{width:120px;height:33px;background:var(--orange);color:#fff;font-size:12.5px;font-weight:700;text-align:center;line-height:31px;border-bottom:3px solid #333}
.services{left:0;top:868px;width:1200px;height:372px;background:var(--orange)}
.notch{left:589px;width:22px;height:11px}
.service{width:160px;text-align:center;color:#fff;font-size:13px;font-weight:700;line-height:17px}
.service .disc{width:104px;height:104px;border-radius:50%;background:#fff;margin:0 auto 18px;display:flex;align-items:center;justify-content:center}
.service.current .disc{background:var(--orange);border:4px solid #fff}
.products{left:0;top:1240px;width:1200px;height:459px;background:var(--grey-bg)}
.card{width:198px;height:168px}
.card .photo{width:198px;height:135px}
.card .label{width:198px;height:33px;background:var(--orange);color:#fff;font-size:13.5px;text-align:center;line-height:33px;white-space:nowrap}
.project{width:198px;height:170px}
.badge{width:32px;height:32px;border-radius:50%;background:var(--orange);border:3px solid #fff;color:#fff;font-size:15px;text-align:center;line-height:26px;right:-10px;top:-10px}
.project .caption{left:12px;right:12px;top:50px;color:#fff;font-size:12px;font-weight:700;line-height:14px;text-align:center}
.footer{left:0;top:2094px;width:1200px;height:69px;background:var(--orange);color:#fff}
.footer .links{left:170px;top:17px;font-size:11.5px;word-spacing:2px}
.footer .copy{left:170px;top:42px;font-size:11.5px}
.footer .follow{left:781px;top:21px;font-size:17px;white-space:nowrap}
.social{top:19px;width:28px;height:28px;border-radius:50%;border:2px solid #fff}
.arrow-ctl{width:24px;height:24px}
</style>
</head>
<body>

<div class="abs topbar">
  <div class="abs contact" style="left:173px">
    <svg width="10" height="12" viewBox="0 0 10 12"><path d="M2 0h2l1 3-1.5 1c.5 1.6 1.6 3 3 3.8L8 6.5l2 1.5v2l-1.5 1.5C4 11 0 6 0 2z" fill="#eee"/></svg>
    <span>123-456-7890</span>
  </div>
  <div class="abs contact" style="left:296px">
    <svg width="13" height="9" viewBox="0 0 13 9"><rect width="13" height="9" fill="#eee"/><path d="M0 0l6.5 5L13 0" fill="none" stroke="#3b3b3b" stroke-width="1.2"/></svg>
    <span>info@rm-installations.example</span>
  </div>
  <div class="abs feedback">FEED BACK</div>
</div>

<header class="abs header">
  <div class="abs brand">RM Installations</div>
  <nav>
    <div class="abs nav active" style="left:523px">HOME</div>
    <div class="abs nav" style="left:611px">ABOUT</div>
    <div class="abs nav" style="left:671px">WHAT WE DO</div>
    <div class="abs nav" style="left:771px">PRODUCTS</div>
    <div class="abs nav" style="left:856px">PAST PROJECTS</div>
    <div class="abs nav" style="left:967px">CONTACT</div>
  </nav>
</header>

<section class="abs hero" role="img" aria-label="Close-up photograph of high-end loudspeakers and amplifier components">
  <div class="abs hero-arrow" style="left:0;border-radius:0 30px 30px 0"></div>
  <div class="abs hero-arrow" style="right:0;border-radius:30px 0 0 30px"></div>
  <h1>We Are Custom Audio Video Company</h1>
</section>

<section class="about">
  <h2 class="abs section-title" style="top:646px">About <em>RM Installations</em></h2>
  <p class="abs about-text">Lorem ipsum dolor sit amet, consectetuer adipiscing elit, sed diam nonummy nibh euismod tincidunt ut laoreet dolore magna aliquam erat volutpat. Ut wisi enim ad minim veniam, quis nostrud exerci tation ullamcorper suscipit lobortis nisl ut aliquip ex ea commodo consequat. Duis autem vel eum iriure dolor in hendrerit in vulputate velit esse molestie consequat, vel illum dolore eu feugiat nulla facilisis at vero erose.</p>
  <div class="abs btn" style="left:539px;top:783px">READ MORE</div>
</section>

<section class="abs services">
  <svg class="abs notch" style="top:0" viewBox="0 0 22 11"><path d="M0 0h22L11 11z" fill="#fff"/></svg>
  <h2 class="abs section-title" style="top:105px;color:#fff">Our services</h2>
  <div class="abs rule" style="top:151px;background:rgba(255,255,255,.35)"></div>
  <svg class="abs arrow-ctl" style="left:121px;top:216px" viewBox="0 0 24 24"><path d="M16 3L7 12l9 9" fill="none" stroke="#7a4a12" stroke-width="3"/></svg>
  <svg class="abs arrow-ctl" style="left:1054px;top:216px" viewBox="0 0 24 24"><path d="M8 3l9 9-9 9" fill="none" stroke="#7a4a12" stroke-width="3"/></svg>

  <div class="abs service current" style="left:144px;top:176px">
    <div class="disc"><svg width="56" height="44" viewBox="0 0 56 44"><path d="M2 14h10L26 2v40L12 30H2z" fill="#333"/><path d="M33 14a10 10 0 010 16M38 8a18 18 0 010 28M43 3a25 25 0 010 38" fill="none" stroke="#333" stroke-width="3"/></svg></div>
    Distributed<br>Video
  </div>
  <div class="abs service" style="left:289px;top:176px">
    <div class="disc"><svg width="60" height="50" viewBox="0 0 60 50"><rect x="10" y="6" width="40" height="18" rx="2" transform="rotate(20 30 15)" fill="none" stroke="#333" stroke-width="3"/><path d="M26 30l4 10h-14M10 32v14" fill="none" stroke="#333" stroke-width="3"/></svg></div>
    Security Camera<br>Systems
  </div>
  <div class="abs service" style="left:438px;top:176px">
    <div class="disc"><svg width="62" height="44" viewBox="0 0 62 44"><rect x="2" y="4" width="16" height="36" fill="#333"/><rect x="44" y="4" width="16" height="36" fill="#333"/><rect x="20" y="16" width="22" height="14" fill="none" stroke="#333" stroke-width="3"/><circle cx="10" cy="28" r="5" fill="#fff"/><circle cx="52" cy="28" r="5" fill="#fff"/><circle cx="10" cy="13" r="3" fill="#fff"/><circle cx="52" cy="13" r="3" fill="#fff"/></svg></div>
    Residential<br>Cinemas
  </div>
  <div class="abs service" style="left:580px;top:176px">
    <div class="disc"><svg width="56" height="56" viewBox="0 0 56 56"><circle cx="28" cy="28" r="10" fill="none" stroke="#333" stroke-width="3"/><path d="M28 18a10 10 0 010 20z" fill="#333"/><g stroke="#333" stroke-width="3"><path d="M28 2v9M28 45v9M2 28h9M45 28h9M9 9l6 6M41 41l6 6M47 9l-6 6M15 41l-6 6"/></g></svg></div>
    Automated<br>Lighting Control
  </div>
  <div class="abs service" style="left:725px;top:176px">
    <div class="disc"><svg width="56" height="52" viewBox="0 0 56 52"><path d="M6 36V26a22 22 0 0144 0v10" fill="none" stroke="#333" stroke-width="4"/><rect x="4" y="30" width="10" height="20" rx="3" fill="#333"/><rect x="42" y="30" width="10" height="20" rx="3" fill="#333"/></svg></div>
    Outdoor Audio<br>and Video
  </div>
  <div class="abs service" style="left:882px;top:176px">
    <div class="disc"><svg width="60" height="48" viewBox="0 0 60 48"><rect x="22" y="2" width="16" height="12" fill="#333"/><path d="M30 14v10M8 24h44M8 24v10M30 24v10M52 24v10" fill="none" stroke="#333" stroke-width="3"/><rect x="0" y="34" width="16" height="12" fill="#333"/><rect x="22" y="34" width="16" height="12" fill="#333"/><rect x="44" y="34" width="16" height="12" fill="#333"/></svg></div>
    Residential<br>Computer Networks
  </div>
</section>

<section class="abs products">
  <svg class="abs notch" style="top:0" viewBox="0 0 22 11"><path d="M0 0h22L11 11z" fill="var(--orange)"/></svg>
  <h2 class="abs section-title" style="top:114px">Our <em>Products</em></h2>
  <div class="abs rule" style="top:160px"></div>
  <svg class="abs arrow-ctl" style="left:121px;top:243px" viewBox="0 0 24 24"><path d="M16 3L7 12l9 9" fill="none" stroke="#777" stroke-width="3"/></svg>
  <svg class="abs arrow-ctl" style="left:1054px;top:243px" viewBox="0 0 24 24"><path d="M8 3l9 9-9 9" fill="none" stroke="#777" stroke-width="3"/></svg>

  <div class="abs card" style="left:170px;top:185px">
    <div class="photo" role="img" aria-label="Security cameras beside a monitor showing camera feeds" style="background:linear-gradient(135deg,#e8e8e8,#6f6f6f)"></div>
    <div class="label">Security Camera Systems</div>
  </div>
  <div class="abs card" style="left:391px;top:185px">
    <div class="photo" role="img" aria-label="Red media room with television and speakers" style="background:linear-gradient(180deg,#c81e1e,#5a0d0d)"></div>
    <div class="label">Media Rooms</div>
  </div>
  <div class="abs card" style="left:611px;top:185px">
    <div class="photo" role="img" aria-label="Outdoor television showing a ball game on a patio" style="background:linear-gradient(180deg,#5a4a3a,#6f8a4a)"></div>
    <div class="label">Outdoor Audio and Video</div>
  </div>
  <div class="abs card" style="left:832px;top:185px">
    <div class="photo" role="img" aria-label="Hand holding a phone controlling living room lights" style="background:linear-gradient(135deg,#a27a3a,#3e2d18)"></div>
    <div class="label">Automated Lighting Control</div>
  </div>

  <div class="abs btn" style="left:539px;top:389px">SEE ALL</div>
</section>

<section class="projects">
  <svg class="abs notch" style="top:1699px" viewBox="0 0 22 11"><path d="M0 0h22L11 11z" fill="var(--grey-bg)"/></svg>
  <h2 class="abs section-title" style="top:1810px">Past <em>Projects</em></h2>
  <div class="abs rule" style="top:1854px"></div>

  <div class="abs project" style="left:170px;top:1885px">
    <div class="abs" role="img" aria-label="Technician wiring a wall panel" style="inset:0;background:linear-gradient(135deg,#6a6a6a,#3a3a3a)"></div>
    <div class="abs caption">Lorem ipsum dolor sit amet, consectetuer adipiscing elit, sed diam nonummy nibh euismod tincidunt ut laoreet dolore magna aliquam erat volutpat lorem</div>
    <div class="abs badge">1</div>
  </div>
  <div class="abs project" style="left:391px;top:1885px">
    <div class="abs" role="img" aria-label="Security monitoring desk with several screens" style="inset:0;background:linear-gradient(135deg,#8aa0b0,#2f3a44)"></div>
    <div class="abs badge">2</div>
  </div>
  <div class="abs project" style="left:611px;top:1885px">
    <div class="abs" role="img" aria-label="Lighting keypad on a wall with a remote" style="inset:0;background:linear-gradient(135deg,#6e5e3a,#3a3220)"></div>
    <div class="abs badge">3</div>
  </div>
  <div class="abs project" style="left:832px;top:1885px">
    <div class="abs" role="img" aria-label="Installer with tools on a ladder" style="inset:0;background:linear-gradient(135deg,#f2f2f2,#2c4a7a)"></div>
    <div class="abs badge">4</div>
  </div>
</section>

<footer class="abs footer">
  <div class="abs links">HOME &nbsp;|&nbsp; ABOUT &nbsp;|&nbsp; WHAT WE DO &nbsp;|&nbsp; PRODUCTS &nbsp;|&nbsp; PAST PROJECTS &nbsp;|&nbsp; CONTACT</div>
  <div class="abs copy">© 2015 rm-installations.example. All Rights Reserved.</div>
  <div class="abs follow">Follow Us on:</div>
  <span class="abs social" style="left:895px"></span>
  <span class="abs social" style="left:931px"></span>
  <span class="abs social" style="left:967px"></span>
  <span class="abs social" style="left:1003px"></span>
</footer>

</body>
</html>
```